Window Treatment business needs website redesigned.

We need a revamp and refresh of our current site www.velmarix.ca
Looking to attract very high end customer. It should be a very simple design with very little text. This site will be visited by prospective homeowners, designers, builders and architects. They should feel that they are dealing with a high-end product selection, where experience, customer service and unique product offering is the focus. The content will be to highlight our services and highlight the manufacturers we sell, using a few rich photos to highlight the products. We should NOT look like we are a very large company. It should NOT have discounts/savings buttons and many menus to choose from. We offer over 15 years experience to narrow the many market options, to provide the right technical solution.
We specialize in products that are not readily available on the market and specifically motorized systems for indoors and outdoors.
Our main suppliers are Kravenholt.com, Dimbrell.com
We carry our own locally manufactured product line of roller shades.
Main product pictures should be of roller shades, outdoor bug screens, awnings and outdoor pergolas.

Reason: I understand that Christmas is coming up real short and many people are extremely busy. If you have a CREATIVE gifting you still want to submit, I look forward to your idea!

Reason: Due to holiday season, we have not had sufficient time to review to make a final decision. Thank you for your patience!

Target Market(s)

High end home owners, designers, builders, architects

Industry/Entity Type

Contractor

Coding

Coded - Design and coding required

Number of Pages Required

3 page

Font styles to use
Sans Serif

Requirements
Must have
• Landing page with full size image like homepage of zolvane.it
• Products page that highlights products with simple product shot image, description and link to manufacturer.
• On main page a scrolling of customer reviews.
• I want a very simple, eye-catching, emotional image for homepage. It does not need to include any product image.
• An image that shows technology combining/meshing with hand craftsmanship.
• Focus is on design.
• http://www.zolvane.it/en/gallery is a great layout and design.
Nice to have
• Logo shape for icons and watermark should be used.
• Look like and have simple motion effects like quorix.com or telvarin.com
Should not have
• Generic/standard looking feel like bluppet.com or mecklorwindow.ca
• No use of green as background only subtle text.
• Lots of text and pages.

```html
<!DOCTYPE html>
<html lang="en">
<head>
<meta charset="utf-8">
<title>Velmarix – Gallery</title>
<link rel="stylesheet" href="https://fonts.googleapis.com/css2?family=Lato:wght@400;700&display=swap">
<style>
:root{
  --green:#8cc152;
  --green-text:#93c45a;
  --ink:#2b2b2b;
  --muted:#777;
  --soft:#b5b5b5;
  --page:#ececec;
  --white:#ffffff;
  --rule:#d6d6d6;
  --card-border:#cfcfcf;
}
*{box-sizing:border-box;margin:0;padding:0}
html,body{width:1200px;height:916px;overflow:hidden}
body{background:var(--page);font-family:'Lato',sans-serif;color:var(--ink);position:relative}

.site-header{position:absolute;left:0;top:0;width:1200px;height:94px;background:var(--white)}
.enquiry{position:absolute;left:40px;top:26px;display:flex;gap:14px;align-items:center}
.enquiry-label{font-size:14px;line-height:18px}
.enquiry-number{font-size:18px;line-height:24px}
.brand{position:absolute;left:462px;top:12px;display:flex;align-items:center;gap:14px}
.brand-mark{width:70px;height:70px;border-radius:50%;border:5px solid var(--ink)}
.brand-name{font-size:40px;line-height:42px;font-weight:400;color:var(--ink);letter-spacing:1px}
.brand-tagline{font-size:14px;color:var(--muted);margin-top:2px}
.main-nav{position:absolute;right:36px;top:30px;display:flex;gap:16px;align-items:flex-end}
.main-nav a{font-size:19px;color:var(--ink);text-decoration:none;line-height:26px;padding:0 3px}
.main-nav a.is-current{background:var(--green);color:var(--white);padding:0 6px;position:relative}
.main-nav a.is-current::before{content:"";position:absolute;left:0;right:0;top:-10px;height:10px;background:var(--green);clip-path:polygon(0 100%,50% 0,100% 100%)}

.page-title{position:absolute;left:0;width:1200px;top:112px;text-align:center;font-size:38px;font-weight:700}

.category-tabs{position:absolute;left:28px;top:180px;width:1136px;height:58px;border-top:1px solid var(--rule);border-bottom:1px solid var(--rule);display:flex;align-items:center}
.category-tabs a{font-size:17px;color:var(--ink);text-decoration:none;padding:3px 11px;border-left:1px solid var(--soft);line-height:22px}
.category-tabs a:first-child{border-left:none}
.category-tabs a.is-active{background:var(--green);color:var(--white);font-weight:700;padding:4px 10px}
.category-tabs a.is-active + a{border-left:none}

.gallery-grid{position:absolute;left:79px;top:266px;display:grid;grid-template-columns:repeat(4,242px);grid-template-rows:repeat(2,242px);column-gap:25px;row-gap:33px}
.gallery-card{background:var(--white);border:1px solid var(--card-border);padding:10px;position:relative}
.gallery-photo{width:100%;height:100%}
.gallery-card.is-hover .overlay{position:absolute;inset:10px;background:rgba(20,18,16,.72);display:flex;align-items:center;justify-content:center;text-align:center;color:var(--green-text);font-size:24px;font-weight:700;line-height:28px;padding:0 20px}

.photo-office{background:linear-gradient(180deg,#dcdcd8 0%,#b9bfb6 45%,#8e9686 100%)}
.photo-dining{background:linear-gradient(160deg,#3a2c22,#1f1812)}
.photo-lounge{background:linear-gradient(180deg,#c9c2b4 0%,#a6998a 50%,#6e5642 100%)}
.photo-bedroom{background:linear-gradient(180deg,#8aa197 0%,#a7b3a6 55%,#c9b9a3 100%)}
.photo-keypad{background:linear-gradient(180deg,#efefef,#dedede)}
.photo-remote{background:linear-gradient(180deg,#d4d4d4,#b2b2b2)}
.photo-wallplate{background:linear-gradient(180deg,#cfcfcf,#bdbdbd)}
.photo-living{background:linear-gradient(180deg,#d8d2c8 0%,#c4bdb3 60%,#a58c74 100%)}

.pager{position:absolute;right:78px;top:815px;display:flex;align-items:center;gap:12px;font-size:16px}
.pager .prev{color:var(--soft);display:flex;align-items:center;gap:8px}
.pager .sep{color:var(--ink)}
.pager .next{color:var(--ink);display:flex;align-items:center;gap:8px}

.site-footer{position:absolute;left:28px;top:868px;width:1136px;height:48px;border-top:1px solid var(--rule);display:flex;align-items:center;justify-content:space-between}
.copyright{font-size:12px;font-weight:700;padding-left:10px}
.footer-nav{display:flex;gap:12px;margin-left:86px}
.footer-nav a{font-size:12px;font-weight:700;color:var(--ink);text-decoration:none}
.social{display:flex;gap:10px;align-items:center}
.social a{display:flex;align-items:center;gap:4px;font-size:12px;font-weight:700;color:var(--ink);text-decoration:none}
.social a::before{content:"";width:14px;height:14px;border-radius:50%;background:var(--ink)}
</style>
</head>
<body>
<header class="site-header">
  <div class="enquiry">
    <svg width="32" height="32" viewBox="0 0 24 24" aria-hidden="true"><path fill="#8cc152" d="M6.6 10.8c1.4 2.8 3.8 5.1 6.6 6.6l2.2-2.2c.3-.3.7-.4 1-.2 1.1.4 2.3.6 3.6.6.6 0 1 .4 1 1V20c0 .6-.4 1-1 1C10.6 21 3 13.4 3 4c0-.6.4-1 1-1h3.5c.6 0 1 .4 1 1 0 1.3.2 2.5.6 3.6.1.3 0 .7-.2 1L6.6 10.8z"/></svg>
    <div>
      <p class="enquiry-label">For Enquiry Call us</p>
      <p class="enquiry-number">+12 345 678 9012</p>
    </div>
  </div>
  <div class="brand">
    <span class="brand-mark"></span>
    <div>
      <p class="brand-name">Velmarix</p>
      <p class="brand-tagline">Window Treatment Solutions</p>
    </div>
  </div>
  <nav class="main-nav">
    <a href="#">Home</a>
    <a href="#" class="is-current">Gallery</a>
    <a href="#">Conract</a>
  </nav>
</header>

<h1 class="page-title">Gallery</h1>

<nav class="category-tabs">
  <a href="#" class="is-active">Blinds</a>
  <a href="#">Pergolas</a>
  <a href="#">Awnings</a>
  <a href="#">Pavilions</a>
  <a href="#">Drapery</a>
  <a href="#">Fabrics</a>
  <a href="#">Exterior Screens</a>
  <a href="#">More Products</a>
  <a href="#">California Wood Shutters</a>
  <a href="#">Installation Photos</a>
</nav>

<section class="gallery-grid">
  <figure class="gallery-card"><div class="gallery-photo photo-office" role="img" aria-label="Office corridor with roller shades over floor-to-ceiling windows and a green roof outside"></div></figure>
  <figure class="gallery-card is-hover"><div class="gallery-photo photo-dining" role="img" aria-label="Dining room with wood venetian blinds"></div><figcaption class="overlay">Wood Venetian Blinds</figcaption></figure>
  <figure class="gallery-card"><div class="gallery-photo photo-lounge" role="img" aria-label="High-rise living room with sheer shades, yellow sofas and a glass chandelier"></div></figure>
  <figure class="gallery-card"><div class="gallery-photo photo-bedroom" role="img" aria-label="Bedroom with dark wood blinds and a sleigh bed"></div></figure>
  <figure class="gallery-card"><div class="gallery-photo photo-keypad" role="img" aria-label="White wall keypad with open, preset and close buttons"></div></figure>
  <figure class="gallery-card"><div class="gallery-photo photo-remote" role="img" aria-label="Two black shade remote controls on a tabletop stand"></div></figure>
  <figure class="gallery-card"><div class="gallery-photo photo-wallplate" role="img" aria-label="Double white shade control wall plate"></div></figure>
  <figure class="gallery-card"><div class="gallery-photo photo-living" role="img" aria-label="Living room with grey cellular shades and a branch vase"></div></figure>
</section>

<nav class="pager">
  <span class="prev"><svg width="20" height="16" viewBox="0 0 20 16" aria-hidden="true"><path d="M9 2 3 8l6 6M17 2l-6 6 6 6" fill="none" stroke="#b5b5b5" stroke-width="1.6"/></svg>Previous</span>
  <span class="sep">|</span>
  <span class="next">Next<svg width="20" height="16" viewBox="0 0 20 16" aria-hidden="true"><path d="M3 2l6 6-6 6M11 2l6 6-6 6" fill="none" stroke="#2b2b2b" stroke-width="1.6"/></svg></span>
</nav>

<footer class="site-footer">
  <p class="copyright">© 2016, Velmarix. All Rights Reserved.</p>
  <nav class="footer-nav"><a href="#">Home</a><a href="#">Gallery</a><a href="#">Contact</a></nav>
  <div class="social"><a href="#">Folio</a><a href="#">Chirp</a><a href="#">Snapline</a></div>
</footer>
</body>
</html>
```